Business Card - connecting 2 souls and beggining the journey of self discovery

Logo on the front
with tag line

On the back list of services and contact details

Seminars
workshops
Coaching
podcasts

Darren Whitlow
Health & Wellbeing Life Coach
0491 372 615
darren@brightcoreliving.example
brightcoreliving.example

Industry/Entity Type

Life Coaching

Contact Information for Business Card

I like the use of colour from the logo to be used. I'm not a fan of white.

Requirements
Must have
• My tagline: Your path to balance begins within
Nice to have
• Use of colour that is in the mind body soul logo

```html
<!DOCTYPE html>
<html lang="en">
<head>
<meta charset="utf-8">
<title>Brightcore Living – Business Card</title>
<link href="https://fonts.googleapis.com/css2?family=Open+Sans:wght@400;600;700&display=swap" rel="stylesheet">
<style>
  :root {
    --bg: #2a2a2c;
    --card: #ffffff;
    --teal: #3aaa99;
    --grey: #8a8a8c;
    --ink: #3c3c3e;
    --mark: #4fb7a2;
  }
  * { box-sizing: border-box; margin: 0; padding: 0; }
  html, body { width: 1200px; height: 1000px; overflow: hidden; }
  body {
    background: var(--bg);
    font-family: "Open Sans", Arial, sans-serif;
    position: relative;
  }
  .card {
    position: absolute;
    left: 250px;
    width: 700px;
    height: 400px;
    background: var(--card);
    border-radius: 38px;
    overflow: hidden;
  }
  .card--front { top: 70px; }
  .card--back { top: 530px; }

  /* Front */
  .front-brand {
    position: absolute;
    top: 120px; left: 0; right: 0;
    display: flex; flex-direction: column; align-items: center;
  }
  .brand-dot {
    width: 96px; height: 96px; border-radius: 50%;
    background: var(--mark);
  }
  .brand-name {
    font-family: "Open Sans", Arial, sans-serif;
    font-weight: 600;
    color: var(--grey);
    letter-spacing: -1px;
    white-space: nowrap;
  }
  .front-brand .brand-name { font-size: 34px; margin-top: 22px; }
  .tagline {
    position: absolute;
    bottom: 54px; left: 0; right: 0;
    text-align: center;
    color: var(--teal);
    font-size: 13px;
    letter-spacing: 4.5px;
    text-transform: uppercase;
  }

  /* Back */
  .back-title {
    position: absolute; top: 52px; left: 48px;
    font-size: 40px;
  }
  .back-mark {
    position: absolute; top: 96px; right: 50px;
    display: flex; flex-direction: column; align-items: center;
  }
  .back-mark .brand-dot { width: 62px; height: 62px; }
  .back-mark .brand-name { font-size: 19px; margin-top: 10px; letter-spacing: -0.5px; }
  .person {
    position: absolute; top: 176px; left: 80px;
  }
  .person-tab {
    position: absolute; top: 180px; left: 0;
    width: 10px; height: 40px;
    background: var(--teal);
    border-radius: 0 4px 4px 0;
  }
  .person-name {
    color: var(--teal); font-weight: 700; font-size: 24px;
    text-transform: uppercase; letter-spacing: 0.3px;
  }
  .person-role { color: var(--ink); font-size: 19px; margin-top: -2px; }
  .contacts {
    position: absolute; top: 258px; left: 80px;
    list-style: none;
    font-size: 15px; color: var(--ink);
  }
  .contacts li { display: flex; align-items: center; gap: 12px; height: 22px; }
  .contacts svg { width: 14px; height: 14px; fill: none; stroke: var(--teal); stroke-width: 1.6; }
  .contacts .accent { color: var(--teal); }
  .services {
    position: absolute; left: 0; right: 0; bottom: 0;
    height: 44px;
    background: var(--teal);
    color: #fff;
    display: flex; align-items: center; justify-content: center;
    font-size: 15px; letter-spacing: 4px; font-weight: 600;
  }
  .services span.sep { margin: 0 14px; font-weight: 400; }
</style>
</head>
<body>

<section class="card card--front">
  <div class="front-brand">
    <div class="brand-dot"></div>
    <div class="brand-name">Brightcore Living</div>
  </div>
  <p class="tagline">Your path to balance begins within</p>
</section>

<section class="card card--back">
  <div class="brand-name back-title">Brightcore Living</div>

  <div class="back-mark">
    <div class="brand-dot"></div>
    <div class="brand-name">Brightcore Living</div>
  </div>

  <div class="person-tab"></div>
  <div class="person">
    <h1 class="person-name">Darren Whitlow</h1>
    <p class="person-role">Life Coach</p>
  </div>

  <ul class="contacts">
    <li>
      <svg viewBox="0 0 14 14"><rect x="3.5" y="1" width="7" height="12" rx="1.5"/><line x1="6" y1="11" x2="8" y2="11"/></svg>
      <span>0491 372 615</span>
    </li>
    <li>
      <svg viewBox="0 0 14 14"><rect x="1" y="3" width="12" height="8" rx="1"/><polyline points="1,3 7,8 13,3"/></svg>
      <span>darren@brightcoreliving.example</span>
    </li>
    <li>
      <svg viewBox="0 0 14 14"><circle cx="7" cy="7" r="6"/><ellipse cx="7" cy="7" rx="2.5" ry="6"/><line x1="1" y1="7" x2="13" y2="7"/></svg>
      <span>www.<span class="accent">brightcoreliving</span>.example</span>
    </li>
  </ul>

  <div class="services">
    <span>Seminars</span><span class="sep">|</span>
    <span>Workshops</span><span class="sep">|</span>
    <span>Coaching</span><span class="sep">|</span>
    <span>Podcasts</span>
  </div>
</section>

</body>
</html>
```